Quillmont Energy b-card redesign

I would like to redesign the card (and power point template) for quillmont energy. We are a developer/owner/operator of high-tech biomass gasification power plants. We take ag waste like nut shells or fruit pits and convert that into electricity in the 1/2 - 3 MW range. I would like to change our company color from red to golden gate bridge orange (C=0,M=69,,Y=100,B=6).

```html
<!DOCTYPE html>
<html lang="en">
<head>
<meta charset="utf-8">
<title>Quillmont Energy – Business Card</title>
<link rel="stylesheet" href="https://fonts.googleapis.com/css2?family=Questrial&family=Didact+Gothic&display=swap">
<style>
  :root {
    --stage: #1c1c1c;
    --orange: #ee6a12;
    --orange-light: #f28a3c;
    --orange-deep: #d65a0a;
    --paper: #ffffff;
    --ink: #3a3a3a;
    --ink-soft: #666666;
  }
  * { margin: 0; padding: 0; box-sizing: border-box; }
  html, body { width: 1200px; height: 871px; overflow: hidden; }
  body {
    background: var(--stage);
    display: flex;
    align-items: center;
    justify-content: center;
    gap: 40px;
    font-family: "Didact Gothic", "Century Gothic", sans-serif;
  }
  .card {
    width: 540px;
    height: 309px;
    position: relative;
    box-shadow: 0 14px 40px rgba(0,0,0,.55);
  }
  .card--front {
    background: linear-gradient(135deg, var(--orange-light) 0%, var(--orange) 50%, var(--orange-deep) 100%);
    display: flex;
    align-items: center;
    justify-content: center;
  }
  .wordmark {
    font-family: "Questrial", "Century Gothic", sans-serif;
    text-transform: uppercase;
    letter-spacing: 2px;
    font-size: 30px;
    white-space: nowrap;
  }
  .card--front .wordmark { color: #fff6ee; }
  .card--back { background: linear-gradient(160deg, #ffffff 55%, #ececec 100%); }
  .card--back .wordmark {
    position: absolute;
    left: 70px;
    top: 36px;
    color: var(--ink);
    font-size: 28px;
  }
  .contact-list {
    position: absolute;
    left: 36px;
    top: 150px;
    list-style: none;
    font-size: 12.5px;
    color: var(--ink);
    line-height: 22px;
  }
  .contact-list li { display: flex; align-items: center; gap: 12px; }
  .contact-list svg { width: 11px; height: 11px; fill: var(--orange); flex: none; }
  .holder {
    position: absolute;
    right: 36px;
    top: 168px;
    text-align: right;
  }
  .holder-name { color: var(--orange); font-weight: 700; font-size: 16px; font-family: "Questrial", sans-serif; }
  .holder-role { color: var(--ink-soft); font-size: 11px; margin-top: 4px; }
  .address {
    position: absolute;
    right: 36px;
    bottom: 30px;
    text-align: right;
    font-size: 12.5px;
    line-height: 19px;
    color: var(--ink);
  }
</style>
</head>
<body>
  <section class="card card--front">
    <span class="wordmark">Quillmont Energy</span>
  </section>

  <section class="card card--back">
    <span class="wordmark">Quillmont Energy</span>

    <ul class="contact-list">
      <li>
        <svg viewBox="0 0 12 12" aria-hidden="true"><path d="M2.5 1h2l1 2.6-1.3 1a6 6 0 0 0 3.2 3.2l1-1.3L11 7.5v2A1.5 1.5 0 0 1 9.5 11 8.5 8.5 0 0 1 1 2.5 1.5 1.5 0 0 1 2.5 1z"/></svg>
        415.555.0142
      </li>
      <li>
        <svg viewBox="0 0 12 12" aria-hidden="true"><path d="M3 1h6v3H3zM1 5h10v5H9V8H3v2H1zM3.5 9h5v2h-5z"/></svg>
        415.555.0187
      </li>
      <li>
        <svg viewBox="0 0 12 12" aria-hidden="true"><path d="M1 2.5h10v7H1zM1.6 3l4.4 3.4L10.4 3"/></svg>
        corwin@quillmontenergy.net
      </li>
      <li>
        <svg viewBox="0 0 12 12" aria-hidden="true"><circle cx="6" cy="6" r="5"/></svg>
        www.quillmontenergy.net
      </li>
    </ul>

    <div class="holder">
      <div class="holder-name">Martin Hale Corwin</div>
      <div class="holder-role">CEO</div>
    </div>

    <address class="address" style="font-style:normal">
      PO Box 48213<br>
      San Francisco, CA 94120
    </address>
  </section>
</body>
</html>
```